Business Card: RW Office Partners - Your organised problem solver

Business Name: RW Office Partners
Website: www.rwofficepartners.com.au
Email: marisol@rwofficepartners.com.au
Mobile: 61 482 907 236
Facebook: @rwofficepartners
Instrgram: @rwofficepartners

Brading Colours:
HEX
#986474
#ddccd3
#7a8498
#c9d8e4
#000000
#ffffff

Tag Line: Your organised problem solver

Link to DRAFT website:
https://deskhelpcollective.wixsite.com/rw-office-partners

About Page from the website:
My name is Marisol Wrenfield, and I would love to assist you to become more productive in your day to day and achieve your business and personal goals.
My mission is to give you time, time to work on the important tasks of your business or to be able to spend more time with your family. I will take on the tasks you don’t have time for, don’t know well or simply don’t like to do.
I have an extensive background in Administration, Tender Coordination, Document Control, WHS and Quality Management working primarily in the Construction, Mining and Corporate World.
I am passionate about being organised, having order and making things in your life (and mine) easier! I love to watch something unfold and grow into something amazing! I am known for being the go-to problem solver, the organiser of all things, producing high standards of work even under pressure. I’m also a confident communicator, and I understand that you’re busy running your business.

Target Market(s)

Small to Medium Business who require assistance in their business by a virtual assistant.

Industry/Entity Type

Virtual Assistant

Contact Information for Business Card

Mobile: 61 482 907 236

Font styles to use
Sans Serif

Colors
ffffff

Requirements
Must have
• Branding Colours as outlined.
Contact Details as outlined.
Logo as provided.
Proper contact details - mobile, facebook, instragm, website.
Simple, Elegant, very clean looking.
Should not have
• Note cute with pictures.
Not too girly as still want to market to construction companies.

```html
<!DOCTYPE html>
<html lang="en">
<head>
<meta charset="utf-8">
<title>RW Office Partners – Business Card</title>
<link href="https://fonts.googleapis.com/css2?family=Montserrat:wght@500;700&family=Roboto:wght@400;500&display=swap" rel="stylesheet">
<style>
  :root {
    --backdrop: #3b3b3d;
    --card: #1f1e22;
    --mauve: #986474;
    --mauve-soft: #ddccd3;
    --gloss: #5b5a60;
    --white: #ffffff;
  }
  * { box-sizing: border-box; margin: 0; padding: 0; }
  html, body { width: 799px; height: 1200px; overflow: hidden; }
  body {
    background: var(--backdrop);
    font-family: "Roboto", Arial, sans-serif;
    color: var(--white);
    position: relative;
  }
  .card {
    position: absolute;
    left: 80px;
    width: 640px;
    height: 390px;
    background: var(--card);
    border-radius: 4px;
    box-shadow: 0 12px 30px rgba(0,0,0,.45);
    overflow: hidden;
  }
  .card--front { top: 120px; }
  .card--back { top: 690px; }

  /* front */
  .front-wordmark {
    position: absolute;
    left: 60px; right: 40px; top: 100px;
    text-align: center;
    font-family: "Montserrat", Arial, sans-serif;
    font-weight: 700;
    font-size: 50px;
    line-height: 1.1;
    letter-spacing: 1px;
    text-transform: uppercase;
    color: var(--gloss);
  }
  .social-row {
    position: absolute;
    left: 0; right: 0; top: 262px;
    display: flex;
    justify-content: center;
    gap: 22px;
    font-size: 19px;
  }
  .social-item { display: flex; align-items: center; gap: 8px; }
  .social-mark {
    width: 14px; height: 14px;
    border-radius: 3px;
    background: var(--mauve);
    display: inline-block;
  }

  /* back */
  .holder {
    position: absolute; left: 40px; top: 40px;
  }
  .holder-name {
    font-family: "Montserrat", Arial, sans-serif;
    font-weight: 700;
    font-size: 20px;
    color: var(--mauve);
  }
  .holder-role { font-size: 14px; margin-top: 4px; }
  .company {
    position: absolute; left: 40px; top: 140px;
  }
  .company-name {
    font-family: "Montserrat", Arial, sans-serif;
    font-weight: 700;
    font-size: 19px;
    color: var(--mauve);
    margin-bottom: 8px;
  }
  .contact-list { list-style: none; font-size: 16px; line-height: 1.45; }
  .contact-list li { display: flex; align-items: center; gap: 10px; }
  .contact-list svg, .contact-list .social-mark { width: 13px; height: 13px; flex: none; }
  .back-wordmark {
    position: absolute;
    right: 40px; top: 110px;
    width: 230px;
    text-align: right;
    font-family: "Montserrat", Arial, sans-serif;
    font-weight: 700;
    font-size: 46px;
    line-height: 1.05;
    color: var(--mauve);
  }
  .tagline-band {
    position: absolute; right: 0; bottom: 0;
    width: 390px; height: 70px;
  }
  .tagline-band svg { position: absolute; inset: 0; }
  .tagline {
    position: absolute; right: 26px; bottom: 20px;
    font-size: 18px;
    color: var(--white);
  }
</style>
</head>
<body>

<section class="card card--front" aria-label="Card front">
  <div class="front-wordmark">RW Office Partners</div>
  <div class="social-row">
    <span class="social-item"><span class="social-mark"></span>@rwofficepartners</span>
    <span class="social-item"><span class="social-mark"></span>@rwofficepartners</span>
  </div>
</section>

<section class="card card--back" aria-label="Card back">
  <div class="holder">
    <div class="holder-name">Marisol Wrenfield</div>
    <div class="holder-role">Virtual Assistant</div>
  </div>

  <div class="company">
    <div class="company-name">RW Office Partners</div>
    <ul class="contact-list">
      <li>
        <svg viewBox="0 0 16 16" aria-hidden="true"><path fill="#986474" d="M3 1h3l1.5 4-2 1.5a9 9 0 0 0 4 4l1.5-2 4 1.5v3c0 .6-.4 1-1 1A14 14 0 0 1 2 2c0-.6.4-1 1-1z"/></svg>
        61 482 907 236
      </li>
      <li>
        <svg viewBox="0 0 16 16" aria-hidden="true"><rect x="1" y="3" width="14" height="10" rx="1" fill="#986474"/><path d="M1.5 4 8 9l6.5-5" stroke="#1f1e22" stroke-width="1.4" fill="none"/></svg>
        marisol@rwofficepartners.com.au
      </li>
      <li>
        <svg viewBox="0 0 16 16" aria-hidden="true"><g fill="none" stroke="#986474" stroke-width="1.5"><circle cx="8" cy="8" r="6.5"/><ellipse cx="8" cy="8" rx="2.8" ry="6.5"/><path d="M1.5 8h13"/></g></svg>
        www.rwofficepartners.com.au
      </li>
      <li><span class="social-mark"></span>@rwofficepartners</li>
      <li><span class="social-mark"></span>@rwofficepartners</li>
    </ul>
  </div>

  <div class="back-wordmark">RW Office Partners</div>

  <div class="tagline-band">
    <svg viewBox="0 0 390 70" preserveAspectRatio="none" aria-hidden="true">
      <path d="M0 70 C20 20 30 8 70 6 L390 0 L390 70 Z" fill="#986474"/>
    </svg>
    <span class="tagline">Your organised problem solver</span>
  </div>
</section>

</body>
</html>
```